RW Holloway LLC Business Card - Civil Engineering & Consulting Firm

We need a Business Card that is elegant, and masculine.  It is our Professional Civil Engineering & Consulting Company located in San Antonio TX (Not s construction or builder firm- no gears & no tool images please). We provide civil engineering services including  commercial site plans, grading and drainage plans, utility plans, hydraulics and hydrology, land planning, utility coordination, and other general civil engineering services related to commercial and residential development.
We have 2 existing Logos. We would like to convey reliability, strength, trustworthiness and attention to detail.  Blues and orange tones as per logo We are OK with the use of a darker blue in the mix.  We have 2 logo versions - Full Company Name Logo to go on the back of card, & Small Icon Logo for the front w/ personal Info.

Target Market(s)
Architects, Real Estate Developers, Other Strctural Engineers, Surveyers, General Contractors
Industry/Entity Type
Professional Civil Engineering
Contact Information for Business Card
Name, Position, Address, Cell & Office #, email, and company website
Font styles to use
Other font styles liked:
- Avian
Requirements
Should not have
- No Tools, No Gears, no Cranes, or Construction Equipment.

```html
<!DOCTYPE html>
<html lang="en">
<head>
<meta charset="utf-8">
<title>RW Holloway LLC – Business Card</title>
<link href="https://fonts.googleapis.com/css2?family=Arimo&family=Questrial&display=swap" rel="stylesheet">
<style>
  :root {
    --backdrop: #6e6e6e;
    --sky-blue: #7aaed8;
    --signal-orange: #f0912c;
    --ink-black: #171717;
    --paper-white: #ffffff;
    --shadow: rgba(0, 0, 0, 0.85);
  }
  * { margin: 0; padding: 0; box-sizing: border-box; }
  html, body {
    width: 1075px;
    height: 1200px;
    overflow: hidden;
    background: var(--backdrop);
  }
  .card {
    position: absolute;
    left: 206px;
    width: 663px;
    height: 395px;
    box-shadow: 3px 3px 2px var(--shadow);
    overflow: hidden;
  }
  .card--front { top: 187px; background: var(--sky-blue); }
  .card--back { top: 637px; height: 397px; background: var(--ink-black); }

  .accent-panel {
    position: absolute;
    top: 0;
    left: 472px;
    width: 191px;
    height: 100%;
    background: var(--signal-orange);
  }

  .contact {
    position: absolute;
    left: 35px;
    top: 91px;
    color: var(--paper-white);
    font-family: "Arimo", Arial, sans-serif;
  }
  .contact__name {
    font-family: "Questrial", "Century Gothic", sans-serif;
    font-size: 24px;
    font-weight: 400;
    line-height: 1;
    letter-spacing: 0.2px;
  }
  .contact__role {
    font-size: 18px;
    line-height: 1.2;
    margin-top: 2px;
  }
  .contact__lines {
    list-style: none;
    margin-top: 21px;
    font-size: 17.5px;
  }
  .contact__lines li {
    display: flex;
    align-items: center;
    height: 23.5px;
  }
  .contact__lines svg {
    width: 16px;
    height: 16px;
    margin-right: 7px;
    flex: none;
  }
  .contact__address {
    margin-top: 29px;
    font-size: 17.5px;
    line-height: 23.5px;
    font-style: normal;
  }

  .wordmark {
    position: absolute;
    left: 0;
    right: 0;
    top: 176px;
    display: flex;
    justify-content: center;
    align-items: center;
    gap: 16px;
  }
  .wordmark__square {
    width: 22px;
    height: 22px;
    background: var(--signal-orange);
  }
  .wordmark__name {
    font-family: "Questrial", "Century Gothic", sans-serif;
    font-size: 44px;
    letter-spacing: 4px;
    color: var(--sky-blue);
    text-transform: uppercase;
    line-height: 1;
  }
</style>
</head>
<body>
  <section class="card card--front" aria-label="Business card front">
    <div class="accent-panel"></div>
    <div class="contact">
      <h1 class="contact__name">DANIEL MERCER</h1>
      <p class="contact__role">Managing Director</p>
      <ul class="contact__lines">
        <li>
          <svg viewBox="0 0 16 16" aria-hidden="true"><path d="M3.5 1.5l2.5 3-1.5 1.5c.8 2 2.5 3.7 4.5 4.5L10.5 9l3 2.5-1.5 2.5C6.5 14 2 9.5 1.5 3z" fill="none" stroke="#fff" stroke-width="1.6" stroke-linejoin="round"/></svg>
          210-555 014 827
        </li>
        <li>
          <svg viewBox="0 0 16 16" aria-hidden="true"><rect x="1" y="3.5" width="14" height="9.5" fill="#fff"/><path d="M1 3.5l7 5.5 7-5.5" fill="none" stroke="#7aaed8" stroke-width="1.2"/></svg>
          info@hollowayce.com
        </li>
        <li>
          <svg viewBox="0 0 16 16" aria-hidden="true"><g fill="none" stroke="#fff" stroke-width="1.3"><circle cx="8" cy="8" r="6.5"/><ellipse cx="8" cy="8" rx="2.8" ry="6.5"/><path d="M1.5 8h13M2.6 4.6h10.8M2.6 11.4h10.8"/></g></svg>
          www.hollowayce.com
        </li>
      </ul>
      <address class="contact__address">618, Briarwood Crest Drive<br>78216,San Antonio TX</address>
    </div>
  </section>

  <section class="card card--back" aria-label="Business card back">
    <div class="wordmark">
      <span class="wordmark__square"></span>
      <span class="wordmark__name">RW Holloway LLC</span>
    </div>
  </section>
</body>
</html>
```